Mara Penrith Copywriter Website

I am starting a new business as a freelance copywriter. Trying to set up the website for my business is proving to be too technical for me. I would like a simple, clean website using primarily black and white. I have attached the logo I would like used. I would like the menu icons to be Home, Services, Portfolio, Blog, Contact. I would like my mobile phone number (0412 583 906) and email address (mara.penrith.copywriter@fernmail.test) used in the header of the site. I need the site to be easily manageable and inter-changeable for me to be able to move things around and add images, etc with ease.

I would like the home page to be a static page with space for an image of myself somewhere (I haven't had this taken as yet), an area to put a bit about myself and my business, and also somewhere to include social media icons/links. Again, I would like the whole website and home page to be easily managed so that I can add/delete things with ease.

I would like the image of the typewriter used in the website somewhere also please.

Coding

Coded - Design and coding required

Number of Pages Required

5+ page

Font styles to use
Sans Serif
Script

Colors
fdf0f6

Requirements
Must have
• The logo provided
• Ability to change page contents easily
• Ability to add social media icons as needed
Nice to have
• Use of the typewriter image
Should not have
• Complicated pages that are not easily editable

```html
<!DOCTYPE html>
<html lang="en">
<head>
<meta charset="utf-8">
<title>Mara Penrith Copywriter</title>
<link href="https://fonts.googleapis.com/css2?family=Montserrat:wght@400;600;700&family=Lato:wght@400;700&display=swap" rel="stylesheet">
<style>
:root{
  --ink:#111111;
  --text:#444444;
  --muted:#8a8a8a;
  --line:#dddddd;
  --white:#ffffff;
  --blush:#fdf0f6;
  --blush-deep:#f1dde6;
  --panel:#f4f4f4;
  --nav-active:#5a5a5a;
}
*{margin:0;padding:0;box-sizing:border-box}
html,body{width:1200px;height:3828px;overflow:hidden;background:var(--white)}
body{font-family:'Lato',sans-serif;color:var(--text);position:relative}
.abs{position:absolute}
.heading{font-family:'Montserrat',sans-serif;font-weight:700;color:var(--ink);text-transform:uppercase;letter-spacing:1px}
.section-title{position:absolute;left:0;width:1200px;text-align:center;font-size:40px}
.btn{position:absolute;background:var(--ink);color:var(--white);font-family:'Montserrat',sans-serif;font-weight:600;font-size:20px;letter-spacing:1px;border-radius:10px;display:flex;align-items:center;justify-content:center;text-transform:uppercase}

/* header */
.site-header{position:absolute;top:0;left:0;width:1200px;height:132px;background:var(--white)}
.brand{position:absolute;left:70px;top:34px;display:flex;align-items:center;gap:14px}
.brand-dot{width:22px;height:22px;border-radius:50%;background:var(--blush-deep)}
.brand-name{font-family:'Montserrat',sans-serif;font-weight:600;font-size:30px;color:var(--ink);line-height:1.1}
.header-contacts{position:absolute;left:680px;top:42px;width:320px;font-size:13px;color:var(--text);line-height:26px}
.header-contacts div{display:flex;align-items:center;gap:8px;white-space:nowrap}
.social{position:absolute;display:flex;gap:14px}
.social span{width:40px;height:40px;border-radius:50%;border:2px solid var(--line);display:block}
.main-nav{position:absolute;top:132px;left:0;width:1200px;height:56px;background:var(--ink);display:flex;padding-left:80px}
.main-nav a{color:var(--white);text-decoration:none;font-family:'Montserrat',sans-serif;font-weight:600;font-size:17px;padding:0 26px;display:flex;align-items:center;text-transform:uppercase}
.main-nav a.active{background:var(--nav-active)}

/* hero */
.hero{position:absolute;top:188px;left:0;width:1200px;height:600px;background:linear-gradient(180deg,#cfe3ef 0%,#eef3f4 45%,#efe6dc 75%,#e4d6c6 100%)}
.hero-kicker{left:76px;top:200px;font-family:'Montserrat',sans-serif;font-size:22px;color:var(--ink);letter-spacing:2px}
.hero-title{left:72px;top:236px;font-family:'Montserrat',sans-serif;font-size:50px;color:var(--ink);font-weight:400}
.hero-title b{font-weight:700}
.hero-copy{left:76px;top:300px;width:440px;font-size:15px;line-height:22px;color:#333}
.typewriter{left:620px;top:130px;width:520px;height:380px;border-radius:6px;background:linear-gradient(180deg,#4a4a4a,#1c1c1c 60%,#3a3330)}

/* about */
.about-photo{left:60px;top:848px;width:480px;height:572px;background:linear-gradient(180deg,#f5f5f5,#d9cfc6 45%,#e9e9ea)}
.about-title{left:572px;top:852px;font-size:42px}
.about-copy{left:572px;top:920px;width:560px;font-size:15px;line-height:23px}

/* services */
.services{position:absolute;top:1420px;left:0;width:1200px;height:480px;background:linear-gradient(180deg,var(--blush),#f6e7ee)}
.service{position:absolute;width:320px}
.service h3{font-family:'Montserrat',sans-serif;font-weight:600;font-size:22px;color:var(--ink);margin-bottom:6px}
.service p{font-size:14px;line-height:20px}
.service.right-align{text-align:right}
.svc-icon{position:absolute;width:72px;height:72px;border-radius:50%;background:var(--white);border:2px solid var(--line);display:flex;align-items:center;justify-content:center}
.desk-photo{left:460px;top:1612px;width:280px;height:280px;border-radius:50%;background:radial-gradient(circle,#d8d3cf,#9c948f);border:8px solid var(--white)}

/* blog */
.blog{position:absolute;top:1900px;left:0;width:1200px;height:700px;background:var(--panel)}
.blog-photo{left:80px;top:2060px;width:496px;height:268px;background:linear-gradient(135deg,#d7d2cc,#8c857f)}
.blog-feature-title{left:80px;top:2350px;font-family:'Montserrat',sans-serif;font-weight:700;font-size:22px;color:var(--ink)}
.meta{font-size:12px;color:var(--text)}
.meta b{color:var(--ink)}
.blog-feature-copy{left:80px;top:2412px;width:496px;font-size:14px;line-height:21px}
.link{font-family:'Montserrat',sans-serif;font-weight:700;font-size:15px;color:var(--ink);text-decoration:underline;text-transform:uppercase}
.post{position:absolute;left:608px;width:512px;height:112px;background:var(--white);border:1px solid var(--line);display:flex}
.post-date{width:76px;height:100%;background:var(--ink);color:var(--white);display:flex;flex-direction:column;align-items:center;justify-content:center}
.post-date strong{font-family:'Montserrat',sans-serif;font-size:30px;line-height:1}
.post-date small{font-size:12px;margin-top:4px}
.post-body{padding:14px 18px;font-size:13px;line-height:19px}
.post-body p{margin-bottom:8px}

/* portfolio */
.portfolio-grid{position:absolute;top:2752px;left:0;width:1200px;height:588px;display:grid;grid-template-columns:repeat(4,300px);grid-template-rows:repeat(2,294px)}
.tile:nth-child(1){background:linear-gradient(135deg,#9aa0a6,#5c6166)}
.tile:nth-child(2){background:linear-gradient(135deg,#c8c8c8,#6f6f6f)}
.tile:nth-child(3){background:linear-gradient(135deg,#7a7d80,#3f4245)}
.tile:nth-child(4){background:linear-gradient(135deg,#e6e3df,#b8b0a8)}
.tile:nth-child(5){background:linear-gradient(135deg,#d8c7b4,#8f7a66)}
.tile:nth-child(6){background:linear-gradient(135deg,#8e8a86,#3e3a37)}
.tile:nth-child(7){background:linear-gradient(135deg,#b9b9bb,#6c6d70)}
.tile:nth-child(8){background:linear-gradient(135deg,#ede6e0,#c0a898)}

/* contact */
.contact-title{left:80px;top:3420px;font-size:28px}
.contact-item{position:absolute;left:80px;display:flex;align-items:center;gap:16px;font-size:14px;line-height:19px}
.field{position:absolute;border-bottom:1px solid #bbb;font-size:14px;color:var(--text);padding-bottom:10px}

.site-footer{position:absolute;top:3760px;left:0;width:1200px;height:68px;background:var(--ink);color:var(--white);display:flex;align-items:center;justify-content:center;font-size:14px}
</style>
</head>
<body>

<header class="site-header">
  <div class="brand"><span class="brand-dot"></span><span class="brand-name">Mara Penrith<br>Copywriter</span></div>
  <div class="header-contacts">
    <div><svg width="18" height="14" viewBox="0 0 18 14"><rect x="1" y="1" width="16" height="12" fill="none" stroke="#333" stroke-width="1.6"/><path d="M1 1l8 7 8-7" fill="none" stroke="#333" stroke-width="1.6"/></svg>mara.penrith.copywriter@fernmail.test</div>
    <div><svg width="18" height="18" viewBox="0 0 24 24"><path d="M6 2l4 4-2 3c1 3 4 6 7 7l3-2 4 4-3 3C10 21 3 14 3 5z" fill="#333"/></svg>0412 583 906</div>
  </div>
  <div class="social" style="left:1034px;top:42px"><span></span><span></span><span></span></div>
</header>

<nav class="main-nav">
  <a class="active" href="#">Home</a><a href="#">About Us</a><a href="#">Services</a><a href="#">Portfolio</a><a href="#">Blog</a><a href="#">Contact</a>
</nav>

<section class="hero">
  <div class="abs hero-kicker">I LOVE TO COPYWRITE</div>
  <h1 class="abs hero-title">I AM <b>MARA PENRITH</b></h1>
  <p class="abs hero-copy">A wonderful serenity has taken possession of my entire soul, like these sweet mornings of spring which I enjoy with my whole heart.</p>
  <div class="btn" style="left:76px;top:380px;width:190px;height:58px">Contact Us</div>
  <div class="abs typewriter" role="img" aria-label="Vintage black typewriter"></div>
</section>

<section>
  <div class="abs about-photo" role="img" aria-label="Portrait of the copywriter holding a tablet"></div>
  <h2 class="abs heading about-title">About Mara Penrith</h2>
  <p class="abs about-copy">Lorem Ipsum is simply dummy text of the printing and typesetting industry. Lorem Ipsum has been the industry's standard dummy text ever since the 1500s, when an unknown printer took a galley of type and scrambled it to make a type specimen book. It has survived not only five centuries, but also the leap into electronic typesetting, remaining essentially unchanged. It was popularised in the 1960s with the release of Letraset sheets containing Lorem Ipsum passages, and more recently with desktop publishing software like Aldus PageMaker including versions of Lorem Ipsum. Lorem ipsum dolor sit amet, consectetur adipiscing elit, sed do eiusmod tempor incididunt ut labore et dolore magna aliqua. Ut enim ad minim veniam, quis nostrud exercitation ullamco laboris nisi ut aliquip ex ea commodo consequat. Duis aute irure dolor in reprehenderit in voluptate velit esse cillum dolore eu fugiat nulla pariatur.</p>
  <div class="btn" style="left:572px;top:1288px;width:190px;height:58px">Contact Us</div>
</section>

<section class="services">
  <h2 class="heading section-title" style="top:56px">Our Services</h2>
</section>
<div class="service right-align" style="left:138px;top:1588px"><h3>SEO Articles</h3><p>Lorem Ipsum is simply dummy text of the printing and type</p></div>
<div class="svc-icon" style="left:466px;top:1590px"><svg width="34" height="34" viewBox="0 0 34 34"><rect x="7" y="4" width="20" height="26" fill="none" stroke="#111" stroke-width="2.4"/><path d="M11 11h12M11 16h12M11 21h8" stroke="#111" stroke-width="2.2"/></svg></div>
<div class="svc-icon" style="left:632px;top:1590px"><svg width="36" height="36" viewBox="0 0 36 36"><circle cx="18" cy="18" r="4" fill="#111"/><circle cx="6" cy="8" r="3" fill="#111"/><circle cx="30" cy="8" r="3" fill="#111"/><circle cx="6" cy="28" r="3" fill="#111"/><circle cx="30" cy="28" r="3" fill="#111"/><path d="M8 10l8 6M28 10l-8 6M8 26l8-6M28 26l-8-6" stroke="#111" stroke-width="1.6"/></svg></div>
<div class="service" style="left:724px;top:1588px"><h3>Social Copywriting</h3><p>Lorem Ipsum is simply dummy text of the printing and type</p></div>
<div class="service right-align" style="left:26px;top:1730px"><h3>Blogging</h3><p>Lorem Ipsum is simply dummy text of the printing and type</p></div>
<div class="svc-icon" style="left:356px;top:1732px"><svg width="34" height="34" viewBox="0 0 34 34"><rect x="4" y="6" width="26" height="22" fill="none" stroke="#111" stroke-width="2.4"/><path d="M8 12h10M8 17h18M8 22h14" stroke="#111" stroke-width="2"/></svg></div>
<div class="abs desk-photo" role="img" aria-label="Desk with laptop and coffee seen from above"></div>
<div class="svc-icon" style="left:780px;top:1732px"><svg width="34" height="34" viewBox="0 0 34 34"><rect x="5" y="5" width="24" height="24" fill="none" stroke="#111" stroke-width="2.4"/><rect x="9" y="9" width="8" height="7" fill="#111"/><path d="M20 11h6M20 15h6M9 20h17M9 24h17" stroke="#111" stroke-width="2"/></svg></div>
<div class="service" style="left:870px;top:1730px"><h3>Press Release Writing</h3><p>Lorem Ipsum is simply dummy text of the printing and type</p></div>

<section class="blog">
  <h2 class="heading section-title" style="top:64px">Blog Update</h2>
</section>
<div class="abs blog-photo" role="img" aria-label="Hands typing on a laptop at a desk"></div>
<h3 class="abs blog-feature-title">Lorem Ipsum Simply Dummy Text Printing Industry.</h3>
<div class="abs meta" style="left:80px;top:2388px">Posted by : <b>Jenifer</b> &nbsp; Views: 48 &nbsp; Comments: 72</div>
<p class="abs blog-feature-copy">Lorem Ipsum is simply dummy text of the printing and typesetting industry. Lorem Ipsum has been the industry's standard dummy text ever since the 1500s.</p>
<a class="abs link" style="left:80px;top:2520px">Read More</a>
<article class="post" style="top:2068px"><div class="post-date"><strong>28</strong><small>August</small></div><div class="post-body"><p>Lorem Ipsum is simply dummy text of the printing and typesetting industry standard dummy text ever since 1500s.</p><div class="meta">Posted by : <b>Jenifer</b> &nbsp; Views: 48 &nbsp; Comments: 72</div></div></article>
<article class="post" style="top:2224px"><div class="post-date"><strong>29</strong><small>August</small></div><div class="post-body"><p>Lorem Ipsum is simply dummy text of the printing and typesetting industry standard dummy text ever since 1500s.</p><div class="meta">Posted by : <b>Jenifer</b> &nbsp; Views: 48 &nbsp; Comments: 72</div></div></article>
<article class="post" style="top:2380px"><div class="post-date"><strong>30</strong><small>August</small></div><div class="post-body"><p>Lorem Ipsum is simply dummy text of the printing and typesetting industry standard dummy text ever since 1500s.</p><div class="meta">Posted by : <b>Jenifer</b> &nbsp; Views: 48 &nbsp; Comments: 72</div></div></article>
<a class="abs link" style="left:620px;top:2520px">More News</a>

<section>
  <h2 class="heading section-title" style="top:2676px">Our Portfolio</h2>
  <div class="portfolio-grid">
    <div class="tile" role="img" aria-label="Writing in a notebook beside a laptop"></div>
    <div class="tile" role="img" aria-label="Close view of typewriter keys"></div>
    <div class="tile" role="img" aria-label="Laptop keyboard in low light"></div>
    <div class="tile" role="img" aria-label="Hands writing on paper at a bright desk"></div>
    <div class="tile" role="img" aria-label="Woman reading a newspaper"></div>
    <div class="tile" role="img" aria-label="Hands on an old typewriter"></div>
    <div class="tile" role="img" aria-label="Coffee cup next to a keyboard"></div>
    <div class="tile" role="img" aria-label="Woman working on a laptop"></div>
  </div>
</section>

<section>
  <h2 class="abs heading contact-title">Get in Touch</h2>
  <div class="contact-item" style="top:3484px"><svg width="18" height="24" viewBox="0 0 18 24"><path d="M9 1C4.6 1 1 4.6 1 9c0 6 8 14 8 14s8-8 8-14c0-4.4-3.6-8-8-8z" fill="#333"/><circle cx="9" cy="9" r="3" fill="#fff"/></svg><span>123, Address, State Name<br>City Name, Zipcode</span></div>
  <div class="contact-item" style="top:3550px"><svg width="18" height="18" viewBox="0 0 24 24"><path d="M6 2l4 4-2 3c1 3 4 6 7 7l3-2 4 4-3 3C10 21 3 14 3 5z" fill="#333"/></svg><span>0412 583 906</span></div>
  <div class="contact-item" style="top:3600px"><svg width="18" height="14" viewBox="0 0 18 14"><rect x="1" y="1" width="16" height="12" fill="none" stroke="#333" stroke-width="1.6"/><path d="M1 1l8 7 8-7" fill="none" stroke="#333" stroke-width="1.6"/></svg><span>mara.penrith.copywriter@fernmail.test</span></div>
  <div class="social" style="left:80px;top:3646px"><span></span><span></span><span></span></div>
  <div class="field" style="left:430px;top:3484px;width:320px">Name Here*</div>
  <div class="field" style="left:790px;top:3484px;width:340px">Email Here*</div>
  <div class="field" style="left:430px;top:3566px;width:700px;height:48px">Message Here*</div>
  <div class="btn" style="left:430px;top:3640px;width:200px;height:58px;font-size:17px">Send Message</div>
</section>

<footer class="site-footer">Copyright © <b>&nbsp;MARA PENRITH&nbsp;</b> 2016 . All Right Reserved.</footer>

</body>
</html>
```